Design my dad a new business card because his current one sucks!

I need a business card designed for my fathers home maintenance business. His customers are individuals (single moms, old people etc.) as well as the occasional business. As such it needs to be accessible to both target audiences.

The front of the card should be dark grey on yellow with the logo and contain the following information:
- Darren Holtwick
- 0488 274 915
- info@brightoakhomecare.com.au
- 0488 274 915

- ABN: 71 284 630 912
- 'Fully Insured'

The reverse should be yellow on dark grey and will have the web address:
- brightoakhomecare.com.au

And a few key services he offers:
GENERAL REPAIRS
PAINTING/TILING/
PAVING &CONCRETING
PRESSURE WASHING
ON-SITE WELDING
DECKING ADDITIONS & REPAIRS
FENCING
FULL BOND CLEANING

This will be first time the logo has been printed so you will need to come up with the best CMYK approximation of the RGB colours to make sure it is a close as possible.

```html
<!DOCTYPE html>
<html lang="en">
<head>
<meta charset="utf-8">
<title>Bright Oak Home Care – Business Card</title>
<link rel="stylesheet" href="https://fonts.googleapis.com/css2?family=Michroma&display=swap">
<style>
  :root {
    --stage: #1f1f1f;
    --card-dark: #2e2e2e;
    --brand-yellow: #f5c400;
    --ink: #2e2e2e;
    --yellow-soft: #e9c23a;
    --mark: #d8d8d8;
  }
  * { margin: 0; padding: 0; box-sizing: border-box; }
  html, body {
    width: 1200px; height: 863px; overflow: hidden;
    background: var(--stage);
    font-family: "Michroma", "Arial", sans-serif;
  }
  .canvas { position: relative; width: 1200px; height: 863px; }
  .card {
    position: absolute; left: 280px;
    width: 640px; height: 366px;
    background: var(--card-dark);
    border-radius: 6px;
    overflow: hidden;
  }
  .card--back { top: 50px; }
  .card--front { top: 447px; }

  .trim-mark { position: absolute; width: 26px; height: 2px; background: var(--mark); }
  .trim-mark--tl { left: 20px; top: 66px; }
  .trim-mark--bl { left: 20px; bottom: 66px; }
  .trim-mark--tr { right: 20px; top: 66px; }
  .trim-mark--br { right: 20px; bottom: 66px; }

  .brand { display: flex; align-items: center; gap: 12px; color: var(--ink); }
  .brand__dot { width: 30px; height: 30px; border-radius: 50%; background: var(--ink); flex: none; }
  .brand__name { font-size: 21px; letter-spacing: 1px; text-transform: uppercase; line-height: 1.15; }

  /* reverse */
  .back-panel {
    position: absolute; left: 56px; top: 30px; width: 528px; height: 306px;
    background: var(--brand-yellow);
    display: flex; flex-direction: column; align-items: center;
    padding-top: 46px;
  }
  .services {
    list-style: none; margin-top: 30px;
    display: grid; grid-template-columns: auto auto; column-gap: 36px; row-gap: 8px;
    font-size: 9.5px; letter-spacing: 0.5px; color: var(--ink); text-transform: uppercase;
  }
  .services li::before { content: "■"; font-size: 6px; margin-right: 7px; vertical-align: 2px; }
  .back-url {
    position: absolute; bottom: 30px; left: 0; right: 0; text-align: center;
    font-size: 13px; color: var(--ink); letter-spacing: 0.5px;
  }

  /* front */
  .front-panel {
    position: absolute; left: 30px; top: 40px; width: 262px; height: 286px;
    background: var(--brand-yellow);
    display: flex; align-items: center; justify-content: center;
  }
  .front-panel .brand__name { font-size: 15px; }
  .front-panel .brand__dot { width: 24px; height: 24px; }
  .front-panel .brand { gap: 10px; }

  .contact {
    position: absolute; right: 30px; top: 40px; width: 300px;
    text-align: right; color: var(--yellow-soft);
  }
  .contact__name { font-size: 19px; font-weight: 400; text-transform: uppercase; letter-spacing: 1px; color: var(--brand-yellow); }
  .contact__role { font-size: 11px; text-transform: uppercase; letter-spacing: 1.5px; margin-top: 4px; }
  .contact__rule { height: 1px; background: var(--yellow-soft); margin: 18px 0 18px 20px; }
  .contact__row { display: flex; justify-content: flex-end; align-items: center; gap: 12px; margin-bottom: 14px; }
  .contact__lines { font-size: 10.5px; line-height: 1.6; letter-spacing: 0.5px; }
  .contact__icon { width: 24px; height: 24px; flex: none; }
</style>
</head>
<body>
<main class="canvas">

  <section class="card card--back" aria-label="Card reverse">
    <span class="trim-mark trim-mark--tl"></span>
    <span class="trim-mark trim-mark--bl"></span>
    <span class="trim-mark trim-mark--tr"></span>
    <span class="trim-mark trim-mark--br"></span>
    <div class="back-panel">
      <div class="brand">
        <span class="brand__dot"></span>
        <span class="brand__name">Bright Oak<br>Home Care</span>
      </div>
      <ul class="services">
        <li>General Repairs</li>
        <li>On-Site Welding</li>
        <li>Painting / Tiling</li>
        <li>Decking Additions &amp; Repairs</li>
        <li>Paving &amp; Concreting</li>
        <li>Fencing</li>
        <li>Pressure Washing</li>
        <li>Full Bond Cleaning</li>
      </ul>
      <p class="back-url">www.brightoakhomecare.com.au</p>
    </div>
  </section>

  <section class="card card--front" aria-label="Card front">
    <div class="front-panel">
      <div class="brand">
        <span class="brand__dot"></span>
        <span class="brand__name">Bright Oak<br>Home Care</span>
      </div>
    </div>

    <div class="contact">
      <h1 class="contact__name">Darren Holtwick</h1>
      <p class="contact__role">Home Maintenance</p>
      <div class="contact__rule"></div>

      <div class="contact__row">
        <p class="contact__lines">ABN: 71 284 630 912<br>Fully Insured</p>
        <svg class="contact__icon" viewBox="0 0 24 24" aria-hidden="true">
          <rect width="24" height="24" rx="4" fill="var(--brand-yellow)"/>
          <path d="M7 12.5l3.2 3.2L17 8.8" fill="none" stroke="var(--card-dark)" stroke-width="2" stroke-linecap="round" stroke-linejoin="round"/>
        </svg>
      </div>

      <div class="contact__row">
        <p class="contact__lines">0488 274 915<br>0488 274 915</p>
        <svg class="contact__icon" viewBox="0 0 24 24" aria-hidden="true">
          <rect width="24" height="24" rx="4" fill="var(--brand-yellow)"/>
          <path d="M8.6 5.5l1.9 2.6c.3.4.2.9-.1 1.2l-1 1c.8 1.6 2.1 2.9 3.7 3.7l1-1c.3-.3.8-.4 1.2-.1l2.6 1.9c.4.3.5.9.2 1.3l-1 1.4c-.4.5-1 .7-1.6.5-4.2-1.300-7.4-4.5-8.7-8.7-.2-.6 0-1.2.5-1.6l1.4-1c.4-.3 1-.2 1.3.2z" fill="var(--card-dark)"/>
        </svg>
      </div>

      <div class="contact__row">
        <p class="contact__lines">info@brightoakhomecare.com.au<br>www.brightoakhomecare.com.au</p>
        <svg class="contact__icon" viewBox="0 0 24 24" aria-hidden="true">
          <rect width="24" height="24" rx="4" fill="var(--brand-yellow)"/>
          <g fill="none" stroke="var(--card-dark)" stroke-width="1.4">
            <circle cx="12" cy="12" r="6.5"/>
            <ellipse cx="12" cy="12" rx="2.8" ry="6.5"/>
            <line x1="5.5" y1="12" x2="18.5" y2="12"/>
            <line x1="6.5" y1="8.6" x2="17.5" y2="8.6"/>
            <line x1="6.5" y1="15.4" x2="17.5" y2="15.4"/>
          </g>
        </svg>
      </div>
    </div>
  </section>

</main>
</body>
</html>
```